Stylish Business Cards Wanted

- DOUBLE SIDED Design Required -

High end, edgy cards for a corporate and personal stylist. Must include logo,
Name: Belinda Harwick
Title: Director and Stylist
telephone : +61 8 7142 5809
email: belinda@theloombriefing.example
website: theloombriefing.example
Tag: Corporate Workwear & Uniform Specialist | Personal Stylist
Would like nice icons for telephone, email, website

Target Market(s)

Businesses wanting stylish uniforms, people wanting stylish wardrobes

Industry/Entity Type

Corporate Workwear Stylist

Contact Information for Business Card

I would like black, white and gold foiling incorporated in the design - possibly a touch of the other colours on my branding guide attached Name: Belinda Harwick Title: Director and Stylist telephone : +61 8 7142 5809 email: belinda@theloombriefing.example website: theloombriefing.example Tag: Corporate Workwear & Uniform Specialist | Personal Stylist Would like nice icons for telephone, email, website

Font styles to use
Other font styles liked:
• Raleway

Colors

Designer to choose colors to be used in the design.

Requirements
Must have
• Gold foil accents

```html
<!DOCTYPE html>
<html lang="en">
<head>
<meta charset="utf-8">
<title>The Loom Briefing – Business Cards</title>
<link rel="stylesheet" href="https://fonts.googleapis.com/css2?family=Open+Sans:wght@400;600&display=swap">
<style>
  :root {
    --backdrop: #3b3b3b;
    --card: #1b1b1b;
    --gold: #c9b77a;
    --gold-edge: #b9a660;
  }
  * { margin: 0; padding: 0; box-sizing: border-box; }
  html, body {
    width: 1200px; height: 801px; overflow: hidden;
    background: var(--backdrop);
    font-family: "Open Sans", Arial, sans-serif;
  }
  .stage {
    position: relative; width: 1200px; height: 801px;
    display: flex; align-items: center; justify-content: center; gap: 48px;
  }
  .card {
    position: relative;
    width: 532px; height: 304px;
    background: var(--card);
    border: 1.5px solid var(--gold-edge);
    color: var(--gold);
  }
  /* Back side: contact details */
  .card-back .identity {
    position: absolute; left: 40px; top: 112px; width: 190px; text-align: right;
  }
  .identity .name {
    font-weight: 600; font-size: 19px; letter-spacing: 0.5px; text-transform: uppercase;
  }
  .identity .title { font-size: 14px; margin-top: 2px; }
  .card-back .divider {
    position: absolute; left: 250px; top: 104px; width: 1px; height: 66px;
    background: var(--gold);
  }
  .card-back .contacts {
    position: absolute; left: 266px; top: 104px; list-style: none;
    font-size: 14px; line-height: 22px;
  }
  .contacts li { display: flex; align-items: center; gap: 8px; }
  .contacts svg { width: 11px; height: 11px; fill: var(--gold); flex: none; }
  .card-back .tagline {
    position: absolute; left: 0; right: 0; bottom: 34px; text-align: center;
    font-size: 14px; letter-spacing: 0.2px;
  }
  /* Front side: brand name */
  .card-front .brand {
    position: absolute; inset: 0;
    display: flex; align-items: center; justify-content: center; gap: 14px;
  }
  .brand .mark { width: 22px; height: 22px; background: var(--gold); }
  .brand .brand-name {
    font-weight: 600; font-size: 40px; letter-spacing: 1px; color: var(--gold);
  }
</style>
</head>
<body>
<main class="stage">
  <section class="card card-back">
    <div class="identity">
      <p class="name">Belinda Harwick</p>
      <p class="title">Director and Stylist</p>
    </div>
    <div class="divider"></div>
    <ul class="contacts">
      <li>
        <svg viewBox="0 0 24 24" aria-hidden="true"><path d="M6.6 10.8a15 15 0 0 0 6.6 6.6l2.2-2.2c.3-.3.7-.4 1-.2 1.1.4 2.3.6 3.6.6.6 0 1 .4 1 1V20c0 .6-.4 1-1 1A17 17 0 0 1 3 4c0-.6.4-1 1-1h3.5c.6 0 1 .4 1 1 0 1.3.2 2.5.6 3.6.1.3 0 .7-.2 1z"/></svg>
        +61 8 7142 5809
      </li>
      <li>
        <svg viewBox="0 0 24 24" aria-hidden="true"><path d="M2 5h20v14H2z M3.5 6.5 12 13l8.5-6.5" fill="none" stroke="currentColor"/><path d="M2 5h20v2l-10 7L2 7z"/><path d="M2 9l10 7 10-7v10H2z"/></svg>
        belinda@theloombriefing.example
      </li>
      <li>
        <svg viewBox="0 0 24 24" aria-hidden="true"><path d="M12 2a10 10 0 1 0 0 20 10 10 0 0 0 0-20zm0 2c1 0 2.3 2 2.8 5H9.2C9.7 6 11 4 12 4zM4.3 11h3.8v2H4.3a8 8 0 0 1 0-2zm4.9 4h5.6c-.5 3-1.8 5-2.8 5s-2.3-2-2.8-5zm6.7-2V11h3.8a8 8 0 0 1 0 2z"/></svg>
        theloombriefing.example
      </li>
    </ul>
    <p class="tagline">Corporate Workwear &amp; Uniform Specialist &nbsp;•&nbsp; Personal Stylist</p>
  </section>

  <section class="card card-front">
    <div class="brand">
      <span class="mark"></span>
      <span class="brand-name">The Loom Briefing</span>
    </div>
  </section>
</main>
</body>
</html>
```